bRu Design Group - architect web site

need a web site to permit potential clients to view our portfolio of work.

Will need lots of photos included.

Industry/Entity Type

Architect

Coding

Coded - Design and coding required

Number of Pages Required

5+ page

Font styles to use
Sans Serif

Requirements
Must have
• photos should be organized by project - perhaps a summary of photos and then click to enlarge? should be simple to operate. should be able to separate interior design from architecture.
• needs to be easy to add more photos in the future.

```html
<!DOCTYPE html>
<html lang="en">
<head>
<meta charset="utf-8">
<title>bRu Design Group</title>
<link rel="stylesheet" href="https://fonts.googleapis.com/css2?family=Open+Sans:wght@400;600;700&family=Roboto:wght@300;400;500;700&display=swap">
<style>
:root{
  --teal:#5b9194;
  --teal-light:#7fb8bb;
  --ink:#222;
  --text:#444;
  --white:#fff;
  --dark:#1f2122;
  --darker:#181a1b;
  --field:#fff;
  --placeholder:#888;
}
*{box-sizing:border-box;margin:0;padding:0}
html,body{width:1200px;height:2365px;overflow:hidden}
body{font-family:"Open Sans",Arial,sans-serif;background:var(--white);color:var(--text)}
h1,h2,h3{font-weight:400}
.page{position:relative;width:1200px;height:2365px;overflow:hidden}
.abs{position:absolute}

/* hero */
.hero{left:0;top:0;width:1200px;height:470px}
.hero-photo{position:absolute;inset:0;background:
  radial-gradient(ellipse at 50% 45%,#5b5d5e 0%,#3a3c3d 45%,#1e2021 100%)}
.topbar{position:absolute;top:11px;left:237px;right:237px;display:flex;justify-content:space-between;font-size:9px;color:#ddd;letter-spacing:.3px}
.topbar .phones span{margin-left:22px}
.brand-top{position:absolute;top:24px;left:0;width:1200px;text-align:center;font-family:"Roboto",sans-serif;font-weight:700;font-size:40px;color:var(--white);letter-spacing:1px}
.nav{position:absolute;top:98px;left:0;width:1200px;display:flex;justify-content:center;font-size:11px;color:var(--white)}
.nav a{color:var(--white);text-decoration:none;padding:0 24px;position:relative}
.nav a+a::before{content:"";position:absolute;left:0;top:3px;width:1px;height:9px;background:#ddd}
.nav a.active{color:var(--teal-light);font-weight:700;text-decoration:underline}
.nav-rule{position:absolute;top:125px;left:380px;width:440px;height:1px;background:rgba(255,255,255,.18)}
.hero-title{position:absolute;top:186px;left:0;width:1200px;text-align:center;font-family:"Roboto",sans-serif;color:var(--white);font-size:27px;line-height:29px;font-weight:300}
.hero-title b{font-weight:700}
.hero-sub{position:absolute;top:250px;left:0;width:1200px;text-align:center;font-size:12px;color:#eee}
.btn-outline{position:absolute;top:292px;left:520px;width:160px;height:43px;border:2px solid var(--teal-light);color:var(--white);font-family:"Roboto",sans-serif;font-size:16px;letter-spacing:2px;display:flex;align-items:center;justify-content:center}

/* welcome */
.band{left:0;top:470px;width:1200px;height:150px;background:linear-gradient(#e2e2e2,#fff)}
.brand-mid{left:0;top:428px;width:1200px;text-align:center;font-family:"Roboto",sans-serif;font-weight:700;font-size:78px;color:var(--teal)}
.welcome{left:0;top:568px;width:1200px;text-align:center;font-family:"Roboto",sans-serif;font-size:23px;font-weight:400;color:var(--ink)}
.welcome span{color:var(--teal)}
.intro{left:258px;top:624px;width:690px;display:flex;justify-content:space-between;font-size:8.6px;line-height:15.5px;text-align:center;color:#555}
.intro div{width:335px}
.intro p+p{margin-top:15px}

/* sections */
.sec-title{left:0;width:1200px;text-align:center;font-family:"Roboto",sans-serif;font-weight:400;color:var(--ink)}
.interior-h{top:806px;font-size:29px}
.interior-s{top:846px;font-size:12px;letter-spacing:7px;color:var(--teal)}
.grid{left:0;width:1200px;display:grid;grid-template-columns:repeat(5,1fr);grid-template-rows:175px 175px;gap:2px;background:#fff}
.grid-int{top:884px;height:352px}
.grid-arch{top:1443px;height:354px;background:#111}
.tile{display:block}
.arch-band{left:0;top:1238px;width:1200px;height:205px;background:radial-gradient(ellipse at 50% 20%,#4a4c4e 0%,#2a2c2d 50%,#1b1d1e 100%)}
.brand-arch{left:0;top:1262px;width:1200px;text-align:center;font-family:"Roboto",sans-serif;font-weight:700;font-size:60px;color:var(--white)}
.arch-s{left:0;top:1367px;width:1200px;text-align:center;font-size:13px;letter-spacing:8px;color:var(--white)}

/* contact */
.contact{left:0;top:1797px;width:1200px;height:505px}
.contact-photo{position:absolute;inset:0;background:radial-gradient(ellipse at 50% 60%,#3d3f40 0%,#2b2d2e 50%,#1c1e1f 100%)}
.contact-h{position:absolute;top:52px;left:0;width:1200px;text-align:center;font-family:"Roboto",sans-serif;font-size:29px;font-weight:400;color:var(--white)}
.field{position:absolute;background:var(--field);font-size:8px;color:var(--placeholder);padding:8px 10px;letter-spacing:.3px}
.f-name{left:256px;top:143px;width:224px;height:28px}
.f-email{left:488px;top:143px;width:224px;height:28px}
.f-phone{left:721px;top:143px;width:224px;height:28px}
.f-msg{left:256px;top:183px;width:689px;height:105px}
.send{position:absolute;left:256px;top:309px;width:689px;height:28px;background:var(--teal);border-radius:4px;color:var(--white);font-size:9px;font-weight:700;display:flex;align-items:center;justify-content:center;letter-spacing:.5px}
.info{position:absolute;top:376px;left:268px;width:665px;display:flex;justify-content:space-between;text-align:center;color:var(--white)}
.info-item{width:150px}
.info-item svg{display:block;margin:0 auto 4px}
.info-item h3{font-size:14px;font-weight:700;margin-bottom:4px}
.info-item p{font-size:11px;line-height:14px;color:#eee}
.footer{left:0;top:2302px;width:1200px;height:63px;background:var(--darker);color:#ccc;font-size:8px}
.footer p{position:absolute;left:257px;top:25px}
</style>
</head>
<body>
<div class="page">

  <header class="hero abs">
    <div class="hero-photo" role="img" aria-label="Dusk photograph of a large white residence, darkened as hero background"></div>
    <div class="topbar">
      <span>E : studio@brudesign.bm</span>
      <span class="phones"><span>T : 441 . 555 . 0148</span><span>C : 441 . 555 . 0273</span><span>F : 441 . 555 . 0391</span></span>
    </div>
    <div class="brand-top">bRu</div>
    <nav class="nav">
      <a class="active">Home</a><a>Interior Design</a><a>Architechture</a><a>Contact Us</a>
    </nav>
    <div class="nav-rule"></div>
    <h1 class="hero-title"><b>bRu</b> DESIGN GROUP<br><b>&amp; BUILDING</b></h1>
    <p class="hero-sub">Lorem Ipsum is simply dummy text of the printing and typesetting industry.</p>
    <div class="btn-outline">READ MORE</div>
  </header>

  <div class="band abs"></div>
  <div class="brand-mid abs">bRu</div>
  <h2 class="welcome abs">Welcome to <span>bRu Design Group.</span></h2>
  <section class="intro abs">
    <div>
      <p>Lorem Ipsum is simply dummy text of the printing and typesetting industry. Lorem Ipsum has been the industry's standard dummy text ever since the 1500s, when an unknown printer took a galley of type and scrambled it to make a type specimen book. It has survived not only five centuries, but also the leap into electronic typesetting, remaining essentially unchanged.</p>
      <p>It was popularised in the 1960s with the release of Lettamark sheets containing Lorem Ipsum passages, and more recently with desktop publishing software like Pagecraft Studio including versions of Lorem Ipsum.</p>
    </div>
    <div>
      <p>It was popularised in the 1960s with the release of Lettamark sheets containing Lorem Ipsum passages, and more recently with desktop publishing software like Pagecraft Studio including versions of Lorem Ipsum.</p>
      <p>Lorem Ipsum is simply dummy text of the printing and typesetting industry. Lorem Ipsum has been the industry's standard dummy text ever since the 1500s, when an unknown printer took a galley of type and scrambled it to make a type specimen book. It has survived not only five centuries, but also the leap into electronic typesetting, remaining essentially unchanged.</p>
    </div>
  </section>

  <h2 class="sec-title interior-h abs">INTERIOR</h2>
  <p class="sec-title interior-s abs">DESIGN</p>
  <section class="grid grid-int abs">
    <div class="tile" role="img" aria-label="Kitchen with pendant lights and white island" style="background:linear-gradient(160deg,#d9d6d0,#6e5e52)"></div>
    <div class="tile" role="img" aria-label="Bathroom with wood vanity and garden window" style="background:linear-gradient(160deg,#c9b49b,#8a6f55)"></div>
    <div class="tile" role="img" aria-label="Dining room with long table and ocean view" style="background:linear-gradient(170deg,#e4e3df,#8a8d84)"></div>
    <div class="tile" role="img" aria-label="Kitchen with timber ceiling beams" style="background:linear-gradient(170deg,#c08a5d,#efeae4 50%,#5a2a1e)"></div>
    <div class="tile" role="img" aria-label="Hallway with grey tile floor" style="background:linear-gradient(170deg,#ece5dc,#4f4a46)"></div>
    <div class="tile" role="img" aria-label="Dining room with chandelier" style="background:linear-gradient(170deg,#d7d4cd,#6d5b4b)"></div>
    <div class="tile" role="img" aria-label="Living room with white sofas and sea view" style="background:linear-gradient(170deg,#e9e8e3,#6e7f86 45%,#b8b3aa)"></div>
    <div class="tile" role="img" aria-label="Lounge with panoramic windows" style="background:linear-gradient(170deg,#cfd4d2,#8f9d8f 50%,#d9d4cb)"></div>
    <div class="tile" role="img" aria-label="Bathroom with freestanding tub" style="background:linear-gradient(170deg,#b8824f,#e8ddcf 50%,#6a4a33)"></div>
    <div class="tile" role="img" aria-label="Spiral staircase under a dome" style="background:radial-gradient(circle at 60% 40%,#e8eef2,#b6c6d1 60%,#2b2b2b)"></div>
  </section>

  <div class="arch-band abs" role="img" aria-label="Dark photograph of a roofline at night"></div>
  <div class="brand-arch abs">bRu</div>
  <p class="arch-s abs">ARCHITECHTURE</p>
  <section class="grid grid-arch abs">
    <div class="tile" role="img" aria-label="House lit at dusk on a lawn" style="background:linear-gradient(180deg,#1f3a66,#26344a 55%,#1e3120)"></div>
    <div class="tile" role="img" aria-label="Cream house with blue sky" style="background:linear-gradient(180deg,#2d5fb0,#e5dcb8 55%,#3f6a2e)"></div>
    <div class="tile" role="img" aria-label="White cottage among palms" style="background:linear-gradient(180deg,#6a93c4,#e2e2dc 50%,#5a6a3a)"></div>
    <div class="tile" role="img" aria-label="Covered terrace at night" style="background:linear-gradient(180deg,#16306a,#2a2f38 55%,#25361e)"></div>
    <div class="tile" role="img" aria-label="Villa with swimming pool" style="background:linear-gradient(180deg,#8fb1d6,#ece3c6 50%,#2b7ea8)"></div>
    <div class="tile" role="img" aria-label="Lit porch with stone path" style="background:linear-gradient(180deg,#2b2624,#8a6a4c 50%,#2f2a26)"></div>
    <div class="tile" role="img" aria-label="White pergola against blue sky" style="background:linear-gradient(160deg,#1c4aa8,#4d7fd0 60%,#d4d7dd)"></div>
    <div class="tile" role="img" aria-label="Arched entrance lit at dusk" style="background:linear-gradient(180deg,#234a8c,#c8a56a 55%,#24344a)"></div>
    <div class="tile" role="img" aria-label="Cottage at twilight by the sea" style="background:linear-gradient(180deg,#3a5a8c,#7a8ca0 45%,#26331f)"></div>
    <div class="tile" role="img" aria-label="Yellow house with deck" style="background:linear-gradient(180deg,#3f7fd0,#e8dc9e 55%,#4d6a35)"></div>
  </section>

  <section class="contact abs">
    <div class="contact-photo" role="img" aria-label="Darkened photograph of a terrace and pool at night"></div>
    <h2 class="contact-h">Contact Us</h2>
    <div class="field f-name">NAME</div>
    <div class="field f-email">EMAIL</div>
    <div class="field f-phone">PHONE NUMBER</div>
    <div class="field f-msg">MESSAGE</div>
    <div class="send">SEND</div>
    <div class="info">
      <div class="info-item">
        <svg width="18" height="16" viewBox="0 0 18 16"><path d="M2 6c0-3 3-4 7-4s7 1 7 4l-3 1-1-2H6L5 7z" fill="#7fb8bb"/><rect x="4" y="8" width="10" height="7" rx="1" fill="#7fb8bb"/><circle cx="9" cy="11.5" r="2" fill="#2b2d2e"/></svg>
        <h3>Phone/Fax</h3>
        <p>T: 441 . 555 . 0148<br>C: 441 . 555 . 0273<br>F: 441 . 555 . 0391</p>
      </div>
      <div class="info-item">
        <svg width="18" height="16" viewBox="0 0 18 16"><rect x="1" y="3" width="16" height="11" fill="#7fb8bb"/><path d="M1 3l8 6 8-6" stroke="#2b2d2e" stroke-width="1.4" fill="none"/></svg>
        <h3>Email</h3>
        <p>studio@brudesign.bm</p>
      </div>
      <div class="info-item">
        <svg width="18" height="16" viewBox="0 0 18 16"><circle cx="9" cy="8" r="6.5" fill="none" stroke="#7fb8bb" stroke-width="2"/><path d="M9 4v4h3" stroke="#7fb8bb" stroke-width="1.6" fill="none"/></svg>
        <h3>Link</h3>
        <p>www.brudesigngroup.com</p>
      </div>
      <div class="info-item">
        <svg width="18" height="16" viewBox="0 0 18 16"><path d="M9 15s-5-5-5-9a5 5 0 0110 0c0 4-5 9-5 9z" fill="#7fb8bb"/><circle cx="9" cy="6" r="2" fill="#2b2d2e"/></svg>
        <h3>Address</h3>
        <p>UNIT 4 HARBOUR HOUSE<br>12 NORTH BAY RD<br>PAGET</p>
      </div>
    </div>
  </section>

  <footer class="footer abs">
    <p>© bRu Design Group. All rights reserved.</p>
  </footer>
</div>
</body>
</html>
```